Refresh of far from plain IT company website

Our web site is starting to show it's age. You can see the existing site here: www.plumbwick.net. As a growing company we want to come across as a dynamic collection of IT experts.

We want to update the design so are open to any colour palette and look, but want to retain our current table logo. We use the logo on our business cards but with a white background - see the attached file, so you don't need to keep the brown or the green.

The design should consider the range of browsers that will be looking at the site - so please show how it will look on a wide screen laptop and a 768x1024 tablet.

We want to add some pages about our team and their skills, probably with photos of each person on the team.

This is an uncoded project - the PSD files of the design is required, not coding.
Updates

Thanks everyone for the submissions so far.  It's a holiday day in the UK today but we will get some feedback on the designs so far out to you.

Target Market(s)

Architects and other creative types looking for IT support

Industry/Entity Type

Business

Font styles to use
Serif
Sans Serif

Requirements
Must have
• Must look good on a laptop and an iPad.

```html
<!DOCTYPE html>
<html lang="en">
<head>
<meta charset="utf-8">
<title>plumbwick – IT Support</title>
<link href="https://fonts.googleapis.com/css2?family=Ubuntu:wght@300;400;500;700&family=Roboto+Condensed:wght@700&display=swap" rel="stylesheet">
<style>
:root{
  --gold:#d8aa00;
  --gold-dark:#b88f00;
  --plum:#94004b;
  --plum-deep:#7e003f;
  --ink:#333;
  --muted:#666;
  --nav:#3c3c3c;
  --line:#d6d6d6;
}
*{margin:0;padding:0;box-sizing:border-box}
html,body{width:1043px;height:1200px;overflow:hidden;background:#fff}
body{position:relative;font-family:"Ubuntu",sans-serif;color:var(--ink)}
.abs{position:absolute}
.top-rule{left:0;top:0;width:1043px;height:4px;background:var(--gold)}
.live-chat{left:815px;top:0;width:114px;height:25px;background:var(--gold);color:var(--plum);font-size:13px;font-weight:500;display:flex;align-items:center;justify-content:center;gap:6px}
.brand{left:114px;top:22px;display:flex;align-items:center;gap:14px}
.brand-mark{width:22px;height:22px;background:var(--gold)}
.brand-name{font-size:54px;font-weight:500;color:var(--plum);letter-spacing:0.5px;line-height:1}
.call{left:758px;top:47px;display:flex;align-items:center;gap:8px}
.call-label{font-size:12px;color:var(--gold);margin-left:3px}
.call-number{font-size:22px;color:var(--plum);line-height:1.1}
.main-nav{left:114px;top:108px;width:815px;height:27px;display:flex;background:linear-gradient(#5a5a5a,#2e2e2e);border-radius:3px 3px 0 0;overflow:hidden}
.main-nav a{color:#fff;text-decoration:none;font-size:12px;font-weight:500;display:flex;align-items:center;justify-content:center;border-right:1px solid #222;box-shadow:inset -1px 0 0 #666}
.main-nav a.is-active{background:var(--gold);color:var(--plum)}
.hero{left:0;top:135px;width:1043px;height:398px;background:radial-gradient(ellipse at 62% 45%,#e8eef5 0%,#a9c3dc 35%,#7ea2c6 65%,#5e86b0 100%)}
.hero-hand{left:560px;top:135px;width:483px;height:330px;background:radial-gradient(ellipse at 75% 35%,#d69a7a 0%,rgba(200,130,100,.5) 40%,rgba(200,130,100,0) 70%)}
.hero-arrow{width:40px;height:40px;border-radius:50%;background:#2b2b2b;border:2px solid #555;color:#fff;font-size:22px;display:flex;align-items:center;justify-content:center;top:294px}
.fade-band{left:0;top:533px;width:1043px;height:380px;background:linear-gradient(#e9e9e9,#fff 100px,#fff 260px,#ececec)}
.services{left:114px;top:444px;width:815px;height:130px;background:#fff;border:1px solid var(--line);box-shadow:0 6px 8px -6px rgba(0,0,0,.25)}
.services-tab{left:444px;top:428px;width:155px;height:33px;background:linear-gradient(#fafafa,#e6e6e6);border-radius:5px 5px 0 0;font-family:"Roboto Condensed",sans-serif;font-size:20px;color:#444;display:flex;align-items:center;justify-content:center;box-shadow:0 -1px 2px rgba(0,0,0,.15)}
.service{width:190px;text-align:center;top:470px}
.service-icon{width:50px;height:50px;border-radius:50%;background:var(--gold);margin:0 auto;display:flex;align-items:center;justify-content:center;box-shadow:0 4px 3px -2px rgba(0,0,0,.3)}
.service-name{font-size:12.5px;font-weight:500;color:#333;margin-top:13px}
.service-sep{top:468px;width:1px;height:104px;background:linear-gradient(rgba(0,0,0,0),#e2e2e2,rgba(0,0,0,0))}
.svc-arrow{top:504px;font-size:18px;color:#444}
.welcome-title{left:117px;top:604px;font-size:18px;font-weight:500;color:#333}
.welcome-title span{color:var(--plum);font-size:23px}
.welcome-rule{left:116px;top:647px;width:516px;border-top:1px dotted #999}
.welcome-text{left:116px;top:654px;width:516px;font-size:11.5px;line-height:16.5px;color:var(--muted);text-align:justify;letter-spacing:.2px}
.welcome-text p+p{margin-top:7px}
.read-more{left:556px;top:766px;font-size:12px;font-weight:700;color:var(--plum)}
.video{left:653px;top:609px;width:276px;height:147px;background:radial-gradient(circle at 50% 55%,#d9d6cf 0%,#9a9792 45%,#3a3a3a 100%)}
.video-play{left:765px;top:657px;width:56px;height:38px;border-radius:5px;background:rgba(60,60,60,.55)}
.video-bar{left:653px;top:756px;width:276px;height:16px;background:linear-gradient(#f2f2f2,#cfcfcf);border:1px solid #aaa;font-size:7px;color:#333;display:flex;align-items:center}
.soft-rule{left:122px;top:811px;width:799px;height:1px;background:linear-gradient(90deg,rgba(0,0,0,0),#ddd,rgba(0,0,0,0))}
.news-bar{left:114px;top:834px;width:815px;height:49px;background:linear-gradient(#fff,#e8e8e8);border:1px solid #d2d2d2;border-radius:3px;box-shadow:0 2px 2px rgba(0,0,0,.12)}
.date{left:126px;top:842px;width:36px;height:36px;background:var(--plum);color:#fff;text-align:center;font-weight:700}
.date-month{background:var(--gold);font-size:10px;height:14px;line-height:14px}
.date-day{font-size:15px;line-height:22px}
.news-text{left:207px;top:840px;width:712px;font-size:11.5px;line-height:17px;color:var(--muted)}
.news-text b{font-weight:500;color:#444}
.view-all{left:852px;top:864px;font-size:12px;font-weight:700;color:var(--plum)}
.footer{left:0;top:914px;width:1043px;height:245px;background:var(--plum);color:#fff}
.f-head{font-size:16px;font-weight:300;color:#fff}
.f-link{font-size:10.5px;color:#fff;letter-spacing:.3px}
.f-link::before{content:"›";color:var(--gold);margin-right:10px;font-size:13px}
.f-divider{top:937px;width:1px;height:130px;background:linear-gradient(rgba(255,255,255,0),rgba(255,255,255,.35),rgba(255,255,255,0))}
.field{background:#fff;border:1px solid #ccc;border-radius:3px;font-size:10px;color:#999;padding:4px 12px}
.btn{background:var(--gold);color:#fff;font-weight:700;font-size:12px;border-radius:3px;display:flex;align-items:center;justify-content:center}
.info{left:619px;width:150px;font-size:11px;line-height:14px;color:#fff}
.info-ico{left:596px}
.social{top:1112px;width:23px;height:23px;border-radius:2px}
.copyright{left:0;top:1159px;width:1043px;height:41px;background:var(--gold);color:#222;font-size:13px;display:flex;align-items:center;justify-content:center}
</style>
</head>
<body>

<div class="abs top-rule"></div>
<div class="abs live-chat">
  <svg width="18" height="14" viewBox="0 0 18 14"><path d="M2 1h10a2 2 0 0 1 2 2v4a2 2 0 0 1-2 2H7l-3 3V9H2a2 2 0 0 1-2-2V3a2 2 0 0 1 2-2z" fill="none" stroke="#94004b" stroke-width="1.6"/></svg>
  LIVE CHAT
</div>

<div class="abs brand">
  <span class="brand-mark"></span>
  <span class="brand-name">plumbwick</span>
</div>

<div class="abs call">
  <svg width="18" height="34" viewBox="0 0 18 34"><path d="M11 2C4 4 2 10 2 17s2 13 9 15l4-6-4-3c-2-3-2-8 0-11l4-3z" fill="#222"/></svg>
  <div>
    <div class="call-label">Call Us</div>
    <div class="call-number">020 7946 0321</div>
  </div>
</div>

<nav class="abs main-nav">
  <a class="is-active" style="width:84px">HOME</a>
  <a style="width:101px">ABOUT US</a>
  <a style="width:120px">WHAT WE DO</a>
  <a style="width:112px">NEWS BLOG</a>
  <a style="width:96px">ARTICLES</a>
  <a style="width:89px">CLIENTS</a>
  <a style="width:104px">PARTNERS</a>
  <a style="width:109px;border-right:0;box-shadow:none">CONTACT US</a>
</nav>

<div class="abs hero" role="img" aria-label="Photo of a hand holding a blue jigsaw puzzle piece above a table of puzzle pieces"></div>
<div class="abs hero-hand"></div>
<div class="abs hero-arrow" style="left:52px">❮</div>
<div class="abs hero-arrow" style="left:961px">❯</div>

<div class="abs fade-band"></div>

<section>
  <div class="abs services"></div>
  <div class="abs services-tab">Our Services</div>
  <div class="abs svc-arrow" style="left:122px">◀</div>
  <div class="abs svc-arrow" style="left:906px">▶</div>
  <div class="abs service-sep" style="left:364px"></div>
  <div class="abs service-sep" style="left:560px"></div>
  <div class="abs service-sep" style="left:759px"></div>

  <div class="abs service" style="left:140px">
    <div class="service-icon"><svg width="28" height="28" viewBox="0 0 28 28"><circle cx="14" cy="14" r="8" fill="none" stroke="#94004b" stroke-width="4" stroke-dasharray="4 2.3"/><circle cx="14" cy="14" r="3.5" fill="#94004b"/></svg></div>
    <div class="service-name">IT Support &amp; Management</div>
  </div>
  <div class="abs service" style="left:361px">
    <div class="service-icon"><svg width="30" height="22" viewBox="0 0 30 22"><path d="M7 20a6 6 0 0 1 0-12 8 8 0 0 1 15-1 6.5 6.5 0 0 1 1 13z" fill="#94004b"/><path d="M15 8l-5 5h3v5h4v-5h3z" fill="#d8aa00"/></svg></div>
    <div class="service-name">Cloud Computing</div>
  </div>
  <div class="abs service" style="left:558px">
    <div class="service-icon"><svg width="28" height="26" viewBox="0 0 28 26"><rect x="2" y="4" width="20" height="14" rx="1" fill="#94004b"/><rect x="10" y="18" width="4" height="4" fill="#94004b"/><rect x="6" y="22" width="12" height="2" fill="#94004b"/><path d="M22 1l2 4 3-1-2 5h-4z" fill="#94004b"/></svg></div>
    <div class="service-name">Disaster Recovery</div>
  </div>
  <div class="abs service" style="left:744px">
    <div class="service-icon"><svg width="26" height="26" viewBox="0 0 26 26"><rect x="2" y="2" width="13" height="13" rx="2" fill="none" stroke="#94004b" stroke-width="3"/><rect x="11" y="11" width="13" height="13" rx="2" fill="none" stroke="#94004b" stroke-width="3"/></svg></div>
    <div class="service-name">Virtualisation</div>
  </div>
</section>

<section>
  <h1 class="abs welcome-title">Welcome to <span>plumbwick</span></h1>
  <div class="abs welcome-rule"></div>
  <div class="abs welcome-text">
    <p>Plumbwick was established with a specific aim: to consistently deliver an advanced and comprehensive IT service for ambitious growing companies across many industry sectors. We aim to provide the very best in service and support, and to aid business growth through the effective and skilled use of modern IT solutions</p>
    <p>Founded in 2003, we have grown rapidly and have delivered successful business solutions to small and medium sized businesses, working with customers across a wide IT spectrum. The knowledge, experience and expertise.</p>
  </div>
  <div class="abs read-more">Read more »</div>

  <div class="abs video" role="img" aria-label="Video still of a team joining hands in a circle, viewed from below"></div>
  <div class="abs video-play"></div>
  <svg class="abs" style="left:784px;top:666px" width="20" height="20" viewBox="0 0 20 20"><path d="M2 1l17 9-17 9z" fill="rgba(255,255,255,.35)"/></svg>
  <div class="abs video-bar">
    <span style="margin:0 6px">▶</span><span style="margin-right:6px">◀)</span><span>0:00 / 0:47</span>
    <span style="flex:1;height:3px;background:#999;margin:0 14px 0 8px;border-radius:2px"></span><span style="margin-right:6px">▭</span>
  </div>
</section>

<div class="abs soft-rule"></div>

<section>
  <div class="abs news-bar"></div>
  <svg class="abs" style="left:176px;top:835px" width="14" height="47" viewBox="0 0 14 47"><path d="M1 0l12 23L1 47" fill="none" stroke="#ddd" stroke-width="2"/></svg>
  <div class="abs date"><div class="date-month">AUG</div><div class="date-day">12</div></div>
  <div class="abs news-text"><b>Duis aute irure dolor</b> in reprehenderit in voluptate velit esse cillum dolore eu fugiat nulla pariatur. Excepteur sint occaecat cupidatat non proident, sunt in culpa qui officia deserunt mollit anim lorem ipsum lorem ispm.</div>
  <div class="abs view-all">View All &gt;&gt;</div>
</section>

<footer>
  <div class="abs footer"></div>

  <h3 class="abs f-head" style="left:115px;top:928px">Quick Links</h3>
  <div class="abs f-link" style="left:114px;top:960px">HOME</div>
  <div class="abs f-link" style="left:114px;top:992px">ABOUT US</div>
  <div class="abs f-link" style="left:114px;top:1024px">WHAT WE DO</div>
  <div class="abs f-link" style="left:114px;top:1056px">NEWS BLOG</div>
  <div class="abs f-link" style="left:221px;top:960px">ARTICLES</div>
  <div class="abs f-link" style="left:221px;top:992px">CLIENTS</div>
  <div class="abs f-link" style="left:221px;top:1024px">PARTNERS</div>
  <div class="abs f-link" style="left:221px;top:1056px">CONTACT US</div>
  <div class="abs f-divider" style="left:326px"></div>

  <h3 class="abs f-head" style="left:350px;top:929px">Quick Contact</h3>
  <div class="abs field" style="left:345px;top:955px;width:208px;height:23px">Name</div>
  <div class="abs field" style="left:345px;top:984px;width:208px;height:23px">Email</div>
  <div class="abs field" style="left:345px;top:1013px;width:208px;height:40px">Message</div>
  <div class="abs btn" style="left:345px;top:1061px;width:59px;height:20px">Submit</div>
  <div class="abs f-divider" style="left:573px"></div>

  <h3 class="abs f-head" style="left:595px;top:929px">Contact Info</h3>
  <svg class="abs info-ico" style="top:962px" width="12" height="16" viewBox="0 0 12 16"><path d="M6 0a6 6 0 0 1 6 6c0 4-6 10-6 10S0 10 0 6a6 6 0 0 1 6-6z" fill="#d8aa00"/><circle cx="6" cy="6" r="2.3" fill="#94004b"/></svg>
  <div class="abs info" style="top:962px">Lorem ipsum dolor sit amet, consectetuer adipiscing elit.</div>
  <svg class="abs info-ico" style="top:1016px" width="14" height="14" viewBox="0 0 14 14"><circle cx="7" cy="7" r="6" fill="none" stroke="#d8aa00" stroke-width="1.5"/><path d="M5 4l1.5 2-1 1 1.5 2 1-1 1.5 1.5-1 1.5C6 10 4 7 4 5z" fill="#d8aa00"/></svg>
  <div class="abs info" style="top:1016px">020 7946 0388</div>
  <svg class="abs info-ico" style="top:1046px" width="14" height="10" viewBox="0 0 14 10"><rect width="14" height="10" fill="#d8aa00"/><path d="M0 0l7 6 7-6" fill="none" stroke="#94004b" stroke-width="1.2"/></svg>
  <div class="abs info" style="top:1044px">info@plumbwick.net</div>
  <div class="abs f-divider" style="left:780px"></div>

  <h3 class="abs f-head" style="left:117px;top:1114px">News Letter</h3>
  <div class="abs field" style="left:227px;top:1113px;width:211px;height:26px;font-size:11px;padding:6px 11px;border:0">Enter e-mail</div>
  <div class="abs btn" style="left:376px;top:1116px;width:59px;height:20px">Submit</div>

  <h3 class="abs f-head" style="left:486px;top:1114px">Follow us</h3>
  <div class="abs social" style="left:569px;background:#3b5a96"></div>
  <div class="abs social" style="left:605px;background:#3fa9e0"></div>
  <div class="abs social" style="left:638px;background:#1173ae"></div>

  <div class="abs copyright">© 2014 plumbwick. All Rights Reserved.</div>
</footer>

</body>
</html>
```